New Innovative Counselling and psychotherapy Service needs Business Card design

Keep it simple and professional. On one side, just company name and logo (perhaps in all blue) and maybe a tag line.

On other side (all white) my name and Qualifications in centre

Industry/Entity Type

Health And Wellness

Contact Information for Business Card

Dara Whelby
Counsellor & Psychotherapist
BSc (Psychol.), BA, Dip. (Couns. & Psych.), PG.Cert (CBT), FGTrK, ONRE

I will also require Mobile no, Email and web site address of which I'll pass on to final designer.

Font styles to use
Sans Serif

Requirements
Must have
• My Logo Only and please use the colours in logo that is in it.
Should not have
• Any other images

```html
<!DOCTYPE html>
<html lang="en">
<head>
<meta charset="utf-8">
<title>Thrive Lane – Business Card</title>
<link href="https://fonts.googleapis.com/css2?family=Roboto:wght@300;400&family=Roboto+Condensed:wght@400;700&display=swap" rel="stylesheet">
<style>
  :root {
    --sky: #3fb0ec;
    --leaf: #8ed15a;
    --ink: #555a60;
    --paper: #fbfbfb;
    --backdrop: #e9ebee;
    --rule: #c9cdd2;
  }
  * { box-sizing: border-box; margin: 0; padding: 0; }
  html, body { width: 1200px; height: 950px; overflow: hidden; }
  body {
    background: var(--backdrop);
    font-family: "Roboto", Arial, sans-serif;
    position: relative;
  }
  .card {
    position: absolute;
    left: 250px;
    width: 700px;
    height: 400px;
    border-radius: 4px;
    box-shadow: 0 6px 18px rgba(0,0,0,.18);
    overflow: hidden;
  }
  /* Front: white side */
  .card--front { top: 50px; background: var(--paper); }
  .brand {
    position: absolute;
    left: 48px; top: 150px;
    width: 262px;
    display: flex; align-items: center; justify-content: center;
  }
  .brand__name {
    font-weight: 300; font-size: 34px; color: var(--ink);
    letter-spacing: .2px; white-space: nowrap;
  }
  .divider {
    position: absolute; left: 330px; top: 60px;
    width: 1px; height: 230px; background: var(--rule);
  }
  .details { position: absolute; left: 362px; top: 68px; }
  .details__name {
    font-family: "Roboto Condensed", Arial, sans-serif;
    font-weight: 700; font-size: 27px; color: var(--sky);
    text-transform: uppercase; letter-spacing: .5px;
  }
  .details__role {
    font-family: "Roboto Condensed", Arial, sans-serif;
    font-weight: 700; font-size: 19px; color: var(--leaf);
    text-transform: uppercase; margin-top: 2px;
  }
  .details__quals {
    font-family: "Roboto Condensed", Arial, sans-serif;
    font-size: 14px; color: var(--leaf); line-height: 1.35; margin-top: 4px;
  }
  .contacts { list-style: none; margin-top: 26px; }
  .contacts li {
    display: flex; align-items: center; gap: 10px;
    font-size: 16px; color: var(--ink); margin-bottom: 6px;
  }
  .contacts svg { width: 15px; height: 15px; flex: none; }
  .band {
    position: absolute; left: 0; bottom: 0; width: 100%; height: 44px;
    display: flex; align-items: stretch;
  }
  .band__tagline {
    flex: 1; background: var(--sky); color: #fff;
    font-size: 17px; display: flex; align-items: center; padding-left: 40px;
    white-space: nowrap;
  }
  .band__accent { width: 120px; background: var(--leaf); }
  /* Back: blue side */
  .card--back {
    top: 500px; background: var(--sky);
    display: flex; align-items: center; justify-content: center;
  }
  .card--back .brand__name {
    color: #fff; font-size: 50px; font-weight: 300;
  }
</style>
</head>
<body>
  <section class="card card--front">
    <div class="brand">
      <span class="brand__name">Thrive Lane</span>
    </div>
    <div class="divider"></div>
    <div class="details">
      <h1 class="details__name">Dara Whelby</h1>
      <p class="details__role">Counsellor &amp; Psychotherapist</p>
      <p class="details__quals">BSc (Psychol.), BA, Dip. (Couns. &amp; Psych.)<br>PG.Cert (CBT), FGTrK, ONRE</p>
      <ul class="contacts">
        <li>
          <svg viewBox="0 0 16 16"><rect x="3" y="1" width="10" height="14" rx="2" fill="none" stroke="#3fb0ec" stroke-width="1.6"/><circle cx="8" cy="12.3" r="1" fill="#3fb0ec"/></svg>
          555 204 7718
        </li>
        <li>
          <svg viewBox="0 0 16 16"><rect x="1" y="3" width="14" height="10" rx="1" fill="#3fb0ec"/><path d="M1.5 3.8 8 9l6.5-5.2" fill="none" stroke="#fff" stroke-width="1.3"/></svg>
          dara@thrivelane.com
        </li>
        <li>
          <svg viewBox="0 0 16 16"><circle cx="8" cy="8" r="7" fill="#3fb0ec"/><path d="M1 8h14M8 1c-3 3-3 11 0 14M8 1c3 3 3 11 0 14" fill="none" stroke="#fff" stroke-width="1"/></svg>
          www.thrivelane.com
        </li>
      </ul>
    </div>
    <div class="band">
      <p class="band__tagline">Caring For Your Psychological Well-Being Is Our Top Priority</p>
      <div class="band__accent"></div>
    </div>
  </section>

  <section class="card card--back">
    <span class="brand__name">Thrive Lane</span>
  </section>
</body>
</html>
```